Information One Page for Email

I am looking for a informative attachment I can send with an introductive email for Meridale Slab Works. Something I can also Mail.

Meridale Slab Works is the leader in Rebar Post Tension Cable Placement and Post Tension Cable repair. Outside of cable placement and repair we do concrete repair, Parking Garage restoration and
Updates

Content

Post Tension Repair and Concrete Restoration
Post-tensioning is a revolutionary method in concrete construction that enhances the strength and durability of structures. However, like all construction ele-ments, post-tension cables can experience wear and damage over time. Ensuring timely and effective repair is crucial for maintaining the safety and integrity of your building.
Why Post-Tension Cable Repair is Essential
1. **Structural Integrity**: Damaged or deteriorated cables can compromise the structural integrity of your building, leading to safety hazards and potential structural failures.
2. **Extended Lifespan**: Regular maintenance and repair of post-tension cables extend the lifespan of your structure, ensuring it remains safe and function-al for years to come.
3. **Cost-Effective**: Addressing cable issues early on prevents more severe damage and costly repairs down the line.
Common Signs of Post-Tension Cable Issues
- Cracks in concrete surfaces
- Unusual noises or popping sounds
- Visible cable ends or broken strands
- Water leakage through cracks
Our Repair Process
1. **Inspection and Assessment**: Our team conducts a thorough inspection to identify the extent of the damage and determine the appropriate repair meth-ods.
2. **Cable Repair or Replacement**: Depending on the severity, we either re-pair the existing cables or replace them with new ones to restore full functional-ity.
3. **Sealing and Protection**: After repairing, we seal the affected areas to protect against moisture and future damage.
4. **Quality Assurance**: We perform rigorous quality checks to ensure the repairs meet industry standards and the structure is safe for use.
Why Choose Us
- **Expertise and Experience**: With years of experience in post-tension cable repair, our team is skilled in handling even the most complex repairs efficiently and effectively.
- **Advanced Technology**: We use the latest technology and materials to ensure durable and long-lasting repairs.
- **Customer Satisfaction**: Our commitment to quality and customer satisfaction sets us apart. We work closely with our clients to ensure their needs are met and expectations exceeded.
Contact Us
If you suspect issues with your post-tension cables or need a routine inspection, don't hesitate to contact us. Our experts are ready to provide the best solutions to keep your structures safe and secure.
Ensure the safety and longevity of your building with our professional post-tension cable repair services. Trust us to deliver quality and reliability every time.

```html
<!DOCTYPE html>
<html lang="en">
<head>
<meta charset="UTF-8">
<title>Meridale Slab Works – Post-Tension Repair &amp; Concrete Restoration</title>
<link href="https://fonts.googleapis.com/css2?family=Libre+Baskerville:wght@400;700&family=Montserrat:wght@400;500;600;700&display=swap" rel="stylesheet">
<style>
  :root{
    --green-dark:#0f6a3c;
    --green:#15703f;
    --band:#1d6a46;
    --band-deep:#175a3b;
    --mint:#c0ddcf;
    --rule:#b9d6c7;
    --ink:#1f1f1f;
    --paper:#ffffff;
    --photo-light:#a9adb0;
    --photo-dark:#4b4f52;
  }
  *{margin:0;padding:0;box-sizing:border-box}
  html,body{width:848px;height:1200px;overflow:hidden;background:var(--paper)}
  body{font-family:"Montserrat",sans-serif;color:var(--ink);position:relative}
  .flyer{position:relative;width:848px;height:1200px;overflow:hidden;background:var(--paper)}
  .abs{position:absolute}

  .brand{left:0;top:0;width:442px;height:173px;display:flex;align-items:center;padding-left:42px;gap:12px}
  .brand-mark{width:18px;height:18px;background:var(--green-dark)}
  .brand-name{font-weight:700;font-size:32px;line-height:1.05;color:var(--green-dark)}

  .hero-photo{left:442px;top:0;width:406px;height:223px;background:linear-gradient(160deg,var(--photo-light) 0%,#7d8285 45%,var(--photo-dark) 100%)}

  .band-left{left:0;top:173px;width:442px;height:50px;background:var(--band)}
  .band-full{left:0;top:223px;width:848px;height:108px;background:linear-gradient(180deg,var(--band) 0%,var(--band-deep) 100%)}
  .banner-title{left:42px;top:190px;font-family:"Libre Baskerville",serif;font-size:31px;line-height:35px;color:#fff;font-weight:400;white-space:nowrap}
  .banner-rule{left:42px;top:277px;width:768px;height:2px;background:#fff}
  .banner-tag{left:42px;top:291px;font-size:18.5px;font-weight:600;color:#fff;white-space:nowrap}

  .col-divider{left:424px;top:361px;width:2px;height:815px;background:var(--rule)}

  .intro{left:42px;top:340px;width:378px;font-size:12.4px;line-height:17.6px}
  .intro p{margin-bottom:4px}
  .intro h3{font-size:13.8px;font-weight:700;margin:1px 0 2px;white-space:nowrap}
  .left-rule{left:42px;top:660px;width:362px;height:2px;background:var(--rule)}

  .sec-head{font-size:18px;line-height:23px;font-weight:700;color:var(--green)}
  .feature{position:absolute;left:36px;width:376px;display:flex;gap:8px}
  .feature svg{width:38px;height:42px;flex:none}
  .feature h4{font-size:15px;font-weight:700;color:var(--green);margin-bottom:4px;white-space:nowrap}
  .feature p{font-size:11.2px;line-height:15.6px}

  .signs{left:444px;top:343px;width:370px}
  .signs ul{margin:10px 0 2px 26px;font-size:12.6px;line-height:18px}
  .signs p{font-size:12.4px;line-height:18.6px}

  .process-bar{left:436px;top:518px;width:412px;height:46px;background:var(--green-dark);color:#fff;font-size:20px;font-weight:700;padding:9px 0 0 17px}
  .step{position:absolute;left:444px;width:372px;display:flex;gap:21px}
  .step-num{width:35px;height:37px;border-radius:4px;background:var(--green-dark);color:#fff;font-weight:700;font-size:16px;display:flex;align-items:center;justify-content:center;flex:none}
  .step h4{font-size:15px;font-weight:700;margin:4px 0 6px;white-space:nowrap}
  .step p{font-size:11.2px;line-height:15.6px}

  .contact{left:436px;top:915px;width:412px;height:285px;background:var(--mint);border-top-left-radius:30px;padding:11px 20px 0 26px}
  .contact h2{font-size:21px;font-weight:600;margin-bottom:9px}
  .contact p{font-size:12.4px;line-height:17px}
  .contact-row{position:absolute;left:29px;display:flex;align-items:center;gap:16px}
  .contact-icon{width:35px;height:36px;border-radius:5px;background:var(--green-dark);display:flex;align-items:center;justify-content:center}
  .contact-icon svg{width:22px;height:22px}
  .phone{font-size:23px;font-weight:700}
  .contact-link{font-size:16px;font-weight:700}
</style>
</head>
<body>
<main class="flyer">
  <header>
    <div class="abs brand">
      <span class="brand-mark"></span>
      <span class="brand-name">Meridale<br>Slab Works</span>
    </div>
    <div class="abs hero-photo" role="img" aria-label="Photo of workers placing post-tension cables across a concrete deck"></div>
    <div class="abs band-left"></div>
    <div class="abs band-full"></div>
    <h1 class="abs banner-title">Post-Tension Repair &amp;<br>Concrete Restoration Services</h1>
    <div class="abs banner-rule"></div>
    <p class="abs banner-tag">Ensuring structural safety. Extending building lifespan.</p>
  </header>

  <div class="abs col-divider"></div>

  <section class="abs intro">
    <p><strong>Meridale Slab Works</strong> is an industry leader in rebar post-tension cable placement and post-tension cable repair. We provide specialized solutions for commercial and residential structures, with additional expertise in concrete repair and parking garage restoration.</p>
    <p>Our team delivers reliable, industry-standard repair methods designed to protect the structural integrity, safety, and longevity of your building.</p>
    <h3>Post-Tension Repair &amp; Concrete Restoration</h3>
    <p>Post-tensioning is a proven construction method that enhances concrete strength and performance. Over time, post-tension cables and surrounding concrete can experience deterioration due to corrosion, moisture intrusion, or structural movement.</p>
    <p>Timely inspection and repair are essential to prevent safety risks, structural damage, and costly long-term repairs.</p>
  </section>
  <div class="abs left-rule"></div>

  <h2 class="abs sec-head" style="left:42px;top:672px;width:340px">Why Post-Tension Cable Repair Is Essential</h2>

  <div class="feature" style="top:737px">
    <svg viewBox="0 0 38 42"><path d="M19 3 L34 8 V20 C34 30 27 36 19 39 C11 36 4 30 4 20 V8 Z" fill="none" stroke="var(--green)" stroke-width="2"/><path d="M19 8 L29 11 V20 C29 27 24 31 19 34 C14 31 9 27 9 20 V11 Z" fill="var(--green)"/><path d="M14 18 H24 M13 22 H25 M15 26 H23" stroke="#fff" stroke-width="1.6"/></svg>
    <div><h4>Structural Integrity</h4><p>Damaged or deteriorated post-tension cables can compromise load capacity and overall structural safety.</p></div>
  </div>
  <div class="feature" style="top:804px">
    <svg viewBox="0 0 38 42"><circle cx="19" cy="22" r="16" fill="none" stroke="var(--green)" stroke-width="1.6"/><path d="M19 22 V12 M19 22 L13 26" stroke="var(--ink)" stroke-width="1.8" stroke-linecap="round"/><path d="M19 8 v2 M19 34 v2 M5 22 h2 M31 22 h2" stroke="var(--green)" stroke-width="1.4"/></svg>
    <div><h4>Extended Lifespan</h4><p>Routine inspection and repair extend the service life of concrete structures and reduce premature failure.</p></div>
  </div>
  <div class="feature" style="top:871px">
    <svg viewBox="0 0 38 42"><path d="M19 3 L34 8 V20 C34 30 27 36 19 39 C11 36 4 30 4 20 V8 Z" fill="none" stroke="var(--green)" stroke-width="2"/><text x="19" y="28" text-anchor="middle" font-family="Montserrat,sans-serif" font-weight="700" font-size="18" fill="var(--green)">$</text></svg>
    <div><h4>Cost-Effective Prevention</h4><p>Early intervention helps avoid extensive structural repairs and significantly higher repair costs.</p></div>
  </div>

  <h2 class="abs sec-head" style="left:42px;top:945px;font-size:19px;white-space:nowrap">Why Choose Meridale Slab Works</h2>

  <div class="feature" style="top:975px">
    <svg viewBox="0 0 38 42"><path d="M6 4 H14 L19 12 L24 4 H32 L24 15 H14 Z" fill="var(--green)"/><circle cx="19" cy="27" r="12" fill="none" stroke="var(--green)" stroke-width="2.2"/><path d="M19 20 L21 25 L26 25 L22 28 L23.5 33 L19 30 L14.5 33 L16 28 L12 25 L17 25 Z" fill="var(--green)"/></svg>
    <div><h4>Proven Expertise</h4><p>Years of specialized experience in post-tension systems, concrete repair, and structural restoration.</p></div>
  </div>
  <div class="feature" style="top:1041px">
    <svg viewBox="0 0 38 42"><g transform="translate(14 20)"><circle r="7" fill="none" stroke="var(--ink)" stroke-width="4"/><path d="M0 -11 V-7 M0 7 V11 M-11 0 H-7 M7 0 H11 M-8 -8 L-5 -5 M5 5 L8 8 M-8 8 L-5 5 M5 -5 L8 -8" stroke="var(--ink)" stroke-width="3.5"/></g><ellipse cx="30" cy="22" rx="5" ry="9" fill="none" stroke="var(--ink)" stroke-width="1.6"/></svg>
    <div><h4>Advanced Technology</h4><p>Use of modern tools, materials, and repair techniques to deliver durable, long-lasting results.</p></div>
  </div>
  <div class="feature" style="top:1108px">
    <svg viewBox="0 0 38 42"><path d="M19 4 L33 9 V20 C33 30 26 35 19 38 C12 35 5 30 5 20 V9 Z" fill="none" stroke="var(--green)" stroke-width="2"/><path d="M12 21 L17 26 L27 15" fill="none" stroke="var(--green)" stroke-width="3" stroke-linecap="round"/></svg>
    <div><h4>Commitment to Quality</h4><p>A focus on safety, precision, and client satisfaction on every project.</p></div>
  </div>

  <section class="abs signs">
    <h2 class="sec-head">Common Signs of Post-Tension Cable Damage</h2>
    <ul>
      <li>Cracks in concrete slabs, beams, or decks</li>
      <li>Visible cable ends or broken strands</li>
      <li>Unusual popping, cracking, or snapping sounds</li>
      <li>Water leakage through cracks or joints</li>
    </ul>
    <p>If any of these conditions are present, a professional assessment is strongly recommended.</p>
  </section>

  <h2 class="abs process-bar">Our Repair Process</h2>

  <div class="step" style="top:586px"><span class="step-num">1</span><div><h4>Inspection &amp; Assessment</h4><p>Our specialists perform a detailed inspection to evaluate cable condition, concrete damage, and structural impact.</p></div></div>
  <div class="step" style="top:670px"><span class="step-num">2</span><div><h4>Cable Repair or Replacement</h4><p>Based on the assessment, damaged cables are repaired or replaced using approved industry methods to restore structural performance.</p></div></div>
  <div class="step" style="top:753px"><span class="step-num">3</span><div><h4>Sealing &amp; Protection</h4><p>Repaired areas are sealed to prevent moisture intrusion and protect against future deterioration.</p></div></div>
  <div class="step" style="top:825px"><span class="step-num">4</span><div><h4>Quality Assurance</h4><p>All work is reviewed to ensure compliance with industry standards and long-term structural safety.</p></div></div>

  <section class="abs contact">
    <h2>Contact Us</h2>
    <p>If you suspect post-tension cable issues or require a professional inspection, our team is ready to assist.</p>
    <div class="contact-row" style="top:93px">
      <span class="contact-icon"><svg viewBox="0 0 24 24"><path d="M6.6 3 L9.5 3.6 L10.5 8 L8.4 9.6 C9.6 12 11.9 14.4 14.4 15.6 L16 13.5 L20.4 14.5 L21 17.4 C21 19.4 19.4 21 17.4 21 C9.4 21 3 14.6 3 6.6 C3 4.6 4.6 3 6.6 3 Z" fill="#fff"/></svg></span>
      <span class="phone">555-014-2290</span>
    </div>
    <div class="contact-row" style="top:142px">
      <span class="contact-icon"><svg viewBox="0 0 24 24"><rect x="3" y="5" width="18" height="14" rx="1.5" fill="none" stroke="#fff" stroke-width="1.8"/><path d="M3.5 6 L12 13 L20.5 6 M3.5 18.5 L9.5 12 M20.5 18.5 L14.5 12" fill="none" stroke="#fff" stroke-width="1.6"/></svg></span>
      <span class="contact-link">info@meridaleslabworks.com</span>
    </div>
    <div class="contact-row" style="top:190px">
      <span class="contact-icon"><svg viewBox="0 0 24 24"><circle cx="12" cy="12" r="9" fill="none" stroke="#fff" stroke-width="1.8"/><ellipse cx="12" cy="12" rx="4" ry="9" fill="none" stroke="#fff" stroke-width="1.6"/><path d="M3 12 H21 M5 7.5 H19 M5 16.5 H19" stroke="#fff" stroke-width="1.5"/></svg></span>
      <span class="contact-link">www.meridaleslabworks.com</span>
    </div>
  </section>
</main>
</body>
</html>
```